Meadowlark Property Review is a leading provider of residential appraisal and home inspection products in S

I need a business card/logo designed that obviously describes my business. We are a residential appraisal and home inspection company in Springfield, MO. We offer residential appraisals, home inspection, pest inspection and radon gas measurement. We have been in business for 18 years and hold state certified residential appraisal licenses and OBREX certified home inspection licenses. I have a logo that I really like and will attach, but would be open to new suggestions. I like more modern designs than traditional and would like a two sided card with our services, licenses and qualifications on the back.

```html
<!DOCTYPE html>
<html lang="en">
<head>
<meta charset="utf-8">
<title>Meadowlark Property Review – Business Card</title>
<link rel="stylesheet" href="https://fonts.googleapis.com/css2?family=Open+Sans:wght@400;600;700&display=swap">
<style>
  :root {
    --bg: #e9e5df;
    --card: #ffffff;
    --ink: #1f1f1f;
    --muted: #4a4a4a;
    --orange: #f08a1c;
    --brown: #9a7b55;
    --gold: #d9ad3c;
  }
  * { box-sizing: border-box; margin: 0; padding: 0; }
  html, body { width: 1200px; height: 913px; overflow: hidden; }
  body {
    background: var(--bg);
    font-family: "Open Sans", Arial, sans-serif;
    color: var(--ink);
    position: relative;
  }
  .card {
    position: absolute;
    width: 560px;
    height: 320px;
    background: var(--card);
    box-shadow: 0 6px 18px rgba(0,0,0,.18);
    overflow: hidden;
  }
  .card--front { left: 50px; top: 90px; }
  .card--back { left: 590px; top: 500px; }

  /* front */
  .front__band { position: absolute; left: 0; top: 0; width: 560px; height: 320px; }
  .front__address {
    position: absolute; right: 40px; top: 24px; width: 260px;
    text-align: right; font-size: 13px; line-height: 1.35; color: var(--muted);
  }
  .front__name {
    position: absolute; right: 40px; top: 94px;
    font-size: 22px; font-weight: 700; letter-spacing: .5px; line-height: 1.2;
  }
  .front__rule { position: absolute; left: 300px; top: 126px; width: 220px; height: 1.5px; background: var(--ink); }
  .front__title {
    position: absolute; right: 40px; top: 131px;
    font-size: 12px; font-weight: 600; color: var(--orange); letter-spacing: 1px;
  }
  .badge { position: absolute; left: 30px; top: 114px; width: 38px; height: 38px; border-radius: 50%; background: var(--gold); }
  .brand {
    position: absolute; display: flex; align-items: center; gap: 10px;
    font-weight: 700; color: var(--brown); font-size: 19px; line-height: 1.15;
  }
  .brand__mark { width: 16px; height: 16px; background: var(--orange); flex: none; }
  .front .brand { left: 86px; top: 110px; width: 200px; }
  .contacts__rule { position: absolute; left: 30px; top: 194px; width: 250px; height: 1.5px; background: var(--ink); }
  .contacts { position: absolute; left: 30px; top: 204px; list-style: none; font-size: 14px; font-weight: 600; line-height: 19px; }
  .contacts li { display: flex; align-items: center; gap: 8px; }
  .contacts svg { width: 12px; height: 12px; flex: none; fill: var(--orange); }

  /* back */
  .back .brand { left: 50%; top: 58px; transform: translateX(-50%); font-size: 22px; white-space: nowrap; }
  .back__accent { position: absolute; left: 150px; top: 100px; width: 260px; height: 3px; background: var(--orange); border-radius: 2px; }
  .services { position: absolute; left: 34px; top: 142px; list-style: none; font-size: 15px; font-weight: 600; line-height: 19px; letter-spacing: .3px; }
  .services li { display: flex; align-items: center; gap: 10px; }
  .services li::before { content: ""; width: 9px; height: 9px; border-radius: 50%; background: var(--orange); }
  .back__intro { position: absolute; left: 34px; right: 30px; top: 264px; font-size: 10px; font-weight: 600; line-height: 1.35; }
</style>
</head>
<body>

<section class="card card--front front" aria-label="Business card front">
  <svg class="front__band" viewBox="0 0 560 320" aria-hidden="true">
    <polygon points="0,312 430,272 560,266 560,320 0,320" fill="#f08a1c"/>
    <polygon points="430,172 560,162 560,266 430,272" fill="#9a7b55"/>
  </svg>
  <p class="front__address">482 W Cedar Lane Suite C Springfield, MO 65807</p>
  <p class="front__name">DANA WHITFIELD</p>
  <div class="front__rule"></div>
  <p class="front__title">OWNER</p>
  <div class="badge" role="img" aria-label="Certification badge"></div>
  <div class="brand"><span class="brand__mark"></span>Meadowlark Property Review</div>
  <div class="contacts__rule"></div>
  <ul class="contacts">
    <li><svg viewBox="0 0 12 12"><path d="M2 1l2 0 1 3-1.5 1a7 7 0 0 0 3.5 3.5L8 7l3 1v2a1 1 0 0 1-1 1A9 9 0 0 1 1 2a1 1 0 0 1 1-1z"/></svg>417-555-0142</li>
    <li><svg viewBox="0 0 12 12"><rect x="3" y="0.5" width="6" height="11" rx="1"/></svg>417-555-0178</li>
    <li><svg viewBox="0 0 12 12"><path d="M0 2h12v8H0z M0 2l6 4 6-4" fill="none" stroke="#f08a1c" stroke-width="1.2"/></svg>info@meadowlarkreview.com</li>
    <li><svg viewBox="0 0 12 12"><circle cx="6" cy="6" r="5.3" fill="none" stroke="#f08a1c" stroke-width="1.2"/><path d="M1 6h10M6 1v10" stroke="#f08a1c" stroke-width="1"/></svg>www.meadowlarkreview.com</li>
  </ul>
</section>

<section class="card card--back back" aria-label="Business card back">
  <div class="brand"><span class="brand__mark"></span>Meadowlark Property Review</div>
  <div class="back__accent"></div>
  <ul class="services">
    <li>APPRAISAL</li>
    <li>HOME INSPECTION</li>
    <li>TERMITE</li>
    <li>RADON</li>
    <li>WELL &amp; SEPTIC INSPECTION</li>
    <li>ENERGY AUDITS</li>
  </ul>
  <p class="back__intro">With years of experience behind us, we're prepared to tackle anything from a first time buyer's starter home or a seasoned buyer purchasing a luxurious dream home</p>
</section>

</body>
</html>
```